Business Card Design for Property Development Company Director

I am looking for a professional and unforgettable business card design for our Director of our Property Development Company.
Please see attached .pptx file to find out what information to include. You don't have to follow the exact format shown in the file - I am interested to see your creative flair using the information provided.

```html
<!DOCTYPE html>
<html lang="en">
<head>
<meta charset="utf-8">
<title>Tallwood Property Group – Business Card</title>
<link rel="stylesheet" href="https://fonts.googleapis.com/css2?family=Lato:wght@400;700&display=swap">
<style>
  :root {
    --backdrop: #3a2a20;
    --card: #ffffff;
    --ink: #5f5f5f;
    --ink-soft: #6e6e6e;
    --brand-blue: #1d5cab;
    --brand-grey: #5a5a5a;
  }
  * { margin: 0; padding: 0; box-sizing: border-box; }
  html, body {
    width: 1200px; height: 848px; overflow: hidden;
    background: var(--backdrop);
    font-family: "Lato", sans-serif;
  }
  .canvas { position: relative; width: 1200px; height: 848px; }
  .card {
    position: absolute; left: 264px; width: 672px; height: 378px;
    background: var(--card);
    box-shadow: 0 6px 18px rgba(0,0,0,.35);
  }
  .card--front { top: 28px; }
  .card--back { top: 442px; }

  .wordmark { display: flex; align-items: center; gap: 12px; position: absolute; }
  .wordmark__square { background: var(--brand-grey); flex: none; }
  .wordmark__name { color: var(--brand-blue); font-weight: 700; letter-spacing: .02em; line-height: 1; }

  .card--front .wordmark { left: 74px; top: 162px; }
  .card--front .wordmark__square { width: 48px; height: 48px; }
  .card--front .wordmark__name { font-size: 34px; }

  .divider {
    position: absolute; left: 348px; top: 126px; width: 2px; height: 126px;
    background: var(--brand-blue);
  }
  .details { position: absolute; left: 369px; top: 122px; color: var(--ink); }
  .details__name { font-size: 21px; font-weight: 700; line-height: 1.1; }
  .details__surname { color: var(--brand-blue); }
  .details__role { font-size: 18px; line-height: 1.25; margin-bottom: 20px; }
  .contact { list-style: none; font-size: 18px; }
  .contact li { display: flex; align-items: center; gap: 7px; height: 23px; }
  .contact svg { width: 12px; height: 12px; fill: var(--brand-blue); flex: none; }
  .licence {
    position: absolute; left: 0; right: 0; top: 324px;
    text-align: center; font-size: 18px; color: var(--ink-soft);
  }

  .tagline {
    position: absolute; left: 0; right: 0; top: 74px;
    text-align: center; font-size: 22px; line-height: 28px; color: var(--ink-soft);
  }
  .card--back .wordmark { left: 50%; top: 180px; transform: translateX(-50%); gap: 18px; }
  .card--back .wordmark__square { width: 74px; height: 74px; }
  .card--back .wordmark__name { font-size: 52px; }
  .invite {
    position: absolute; left: 0; right: 0; top: 312px;
    text-align: center; font-size: 18px; color: var(--ink-soft);
  }
</style>
</head>
<body>
<main class="canvas">
  <section class="card card--front">
    <div class="wordmark">
      <span class="wordmark__square"></span>
      <span class="wordmark__name">TALLWOOD</span>
    </div>
    <div class="divider"></div>
    <div class="details">
      <p class="details__name">Daniel <span class="details__surname">Marsh</span></p>
      <p class="details__role">Director</p>
      <ul class="contact">
        <li>
          <svg viewBox="0 0 24 24" aria-hidden="true"><path d="M6.6 10.8a15.1 15.1 0 0 0 6.6 6.6l2.2-2.2c.3-.3.7-.4 1-.2 1.1.4 2.3.6 3.6.6.6 0 1 .4 1 1V20c0 .6-.4 1-1 1C10.6 21 3 13.4 3 4c0-.6.4-1 1-1h3.5c.6 0 1 .4 1 1 0 1.3.2 2.5.6 3.6.1.3 0 .7-.2 1z"/></svg>
          0400 123 456
        </li>
        <li>
          <svg viewBox="0 0 24 24" aria-hidden="true"><path d="M2 5h20v14H2z M3.5 6.5 12 13l8.5-6.5" fill="none" stroke="#1d5cab" stroke-width="2.5"/><path d="M2 5h20v14H2z"/></svg>
          daniel@tallwoodgroup.com.au
        </li>
        <li>
          <svg viewBox="0 0 24 24" aria-hidden="true"><g fill="none" stroke="#1d5cab" stroke-width="2"><circle cx="12" cy="12" r="10"/><ellipse cx="12" cy="12" rx="4.5" ry="10"/><path d="M2 12h20M4 7h16M4 17h16"/></g></svg>
          www.tallwoodgroup.com.au
        </li>
      </ul>
    </div>
    <p class="licence">Real Estate Lic: 1234567 &amp; 1234568</p>
  </section>

  <section class="card card--back">
    <p class="tagline">Property Development<br>&amp; Site Acquisition Specialists</p>
    <div class="wordmark">
      <span class="wordmark__square"></span>
      <span class="wordmark__name">TALLWOOD</span>
    </div>
    <p class="invite">Ask me about our INVESTMENT &amp; PARTNERSHIP opportunities</p>
  </section>
</main>
</body>
</html>
```